Advertising company unique advertising platform

we need a logo design for a new company based in Australia Melbourne. We develop innovated advertising platform where consumer can use this platform to get regular discount, as business owner they can use this platform for free advertisement. Payment for this advertisement platform only payable every two weeks, when I generate revenue for their business

Industry/Entity Type

Advertising

Contact Information for Business Card

Dale Morven | Co-Founder |Managing Director
Suite 718 240 Wattlebrook Lane Melbourne Vic 3000

ABN 38 614 207 923
Tel: +61 0487 259 318 | Email: dale.morven@plivorantu.com

Font styles to use
Decorative
Script

Requirements
Must have
• Try few different design and some round corner business card
Should not have
• One round corner business card...try 4 different colour background not only black, make sure two side is designed. Be creative so imagine you are giving this to a client make sure has wow factor, if you can also try one design with engrave like all the logo, words look 3d feel
• The word Advertising Platform use attached file font

```html
<!DOCTYPE html>
<html lang="en">
<head>
<meta charset="utf-8">
<title>Kelvaro Hub – Business Card</title>
<link rel="stylesheet" href="https://fonts.googleapis.com/css2?family=Source+Sans+3:wght@400;600&display=swap">
<style>
  :root {
    --page-bg: #6e4a35;
    --card-bg: #2b2b2b;
    --accent-orange: #e8522a;
    --accent-amber: #f39a3c;
    --accent-teal: #2fe0ae;
    --text-light: #f2f2f2;
  }
  html, body {
    margin: 0;
    padding: 0;
    width: 1200px;
    height: 960px;
    overflow: hidden;
    background: var(--page-bg);
    font-family: "Source Sans 3", Arial, sans-serif;
  }
  .canvas {
    position: relative;
    width: 1200px;
    height: 960px;
  }
  .card {
    position: absolute;
    background: var(--card-bg);
    border-radius: 22px;
    box-shadow: 0 6px 14px rgba(0,0,0,0.35);
  }
  .card-front { left: 315px; top: 113px; width: 597px; height: 344px; }
  .card-back  { left: 312px; top: 473px; width: 600px; height: 341px; }

  .brand-name {
    font-weight: 600;
    color: var(--accent-orange);
    margin: 0;
    white-space: nowrap;
  }
  .brand-name span { display: block; }
  .card-front .brand-name {
    position: absolute;
    left: 30px;
    top: 16px;
    font-size: 46px;
    line-height: 48px;
  }
  .brand-mark-large {
    position: absolute;
    left: 372px;
    top: 84px;
    width: 180px;
    height: 180px;
    border-radius: 50%;
    background: linear-gradient(160deg, var(--accent-amber), var(--accent-orange));
  }

  .brand-lockup {
    position: absolute;
    left: 0; right: 0;
    top: 82px;
    display: flex;
    align-items: center;
    justify-content: center;
    gap: 18px;
  }
  .brand-lockup .brand-name { font-size: 44px; line-height: 46px; }
  .brand-dot {
    width: 84px; height: 84px;
    border-radius: 50%;
    background: linear-gradient(160deg, var(--accent-amber), var(--accent-orange));
  }

  .contact {
    position: absolute;
    left: 29px;
    top: 124px;
    margin: 0;
  }
  .person-name, .person-role {
    font-size: 17px;
    line-height: 22px;
    text-transform: uppercase;
    margin: 0;
  }
  .person-name { color: var(--accent-orange); font-weight: 600; }
  .person-role { color: var(--accent-teal); font-weight: 400; }
  .detail-group { margin: 4px 0 0; }
  .detail-group + .detail-group { margin-top: 2px; }
  .detail {
    color: var(--text-light);
    font-size: 15.5px;
    line-height: 21px;
    margin: 0;
  }
</style>
</head>
<body>
<main class="canvas">
  <section class="card card-front" aria-label="Business card front">
    <p class="brand-name"><span>Kelvaro</span><span>Hub</span></p>
    <div class="brand-mark-large" role="img" aria-label="Brand symbol area"></div>
    <div class="contact">
      <p class="person-name">Dale Morven</p>
      <p class="person-role">Co-Founder</p>
      <p class="person-role">Managing Director</p>
      <div class="detail-group">
        <p class="detail">Plivorantu</p>
        <p class="detail">ABN 38 614 207 923</p>
      </div>
      <div class="detail-group">
        <p class="detail">Suite 718 240 Wattlebrook Lane</p>
        <p class="detail">Melbourne Vic 3000</p>
      </div>
      <div class="detail-group">
        <p class="detail">P : +61 0487 259 318</p>
        <p class="detail">dale.morven@plivorantu.com</p>
      </div>
    </div>
  </section>

  <section class="card card-back" aria-label="Business card back">
    <div class="brand-lockup">
      <span class="brand-dot" role="img" aria-label="Brand symbol area"></span>
      <p class="brand-name"><span>Kelvaro</span><span>Hub</span></p>
    </div>
  </section>
</main>
</body>
</html>
```